NEW Modern Sleek Business Card for VR Language Startup

Our startup is using VR to lead the next wave of world language education. We need a two-sided business card that introduces the larger organization (Brightloom Language Inc) and our contact info on one side and shows the product, Glimwoorld, on the other side.

Side 1 (contact info)= Brightloom Logo and Contact info (name, title, phone, email)

Side 2 (product)= Glimworld logo, text, and website
Text= Culturally Immersive Language Learning Games
Website= www.glimworld-play.com

Target Market(s)

Education, Technology

Contact Information for Business Card

Contact info will be updated upon approval of the design. For now, put this as a placeholder.

Perry Dunmore
Founder & CEO
pdunmore@quillpost-mail.net
(555)-014-2286

Font styles to use
Other font styles liked:
• Gibson and Century Gothic are the brand fonts

Requirements
Nice to have
• I would love to see cohesion between the design and colors of the two logos. I have attached a few business card designs that I like, so you can get a feel for my preferred style.

```html
<!DOCTYPE html>
<html lang="en">
<head>
<meta charset="utf-8">
<title>Brightloom Language — Business Card</title>
<link href="https://fonts.googleapis.com/css2?family=Montserrat:wght@400;500;600;700&display=swap" rel="stylesheet">
<style>
  :root {
    --backdrop: #1a1a1a;
    --card: #202020;
    --card-edge: #262626;
    --ink: #ffffff;
    --ink-soft: #e8e8ee;
    --accent: #6b66c9;
    --accent-dot: #ef5a6a;
  }
  * { margin: 0; padding: 0; box-sizing: border-box; }
  html, body {
    width: 1200px; height: 900px; overflow: hidden;
    background: var(--backdrop);
    font-family: "Montserrat", "Century Gothic", sans-serif;
    color: var(--ink);
  }
  .canvas {
    position: relative; width: 1200px; height: 900px;
    display: flex; flex-direction: column; align-items: center;
    justify-content: center; gap: 30px;
  }
  .card {
    width: 700px; height: 400px;
    background: linear-gradient(135deg, var(--card) 0%, var(--card-edge) 60%, var(--card) 100%);
    box-shadow: 0 14px 30px rgba(0,0,0,0.55);
    position: relative;
  }
  .brand { display: flex; align-items: center; gap: 14px; }
  .brand-mark {
    width: 22px; height: 22px; border-radius: 50%;
    background: var(--accent-dot); flex: none;
  }
  .brand-name {
    font-weight: 600; font-size: 30px; letter-spacing: 0.14em;
    text-transform: uppercase; line-height: 1.25; color: var(--ink);
    white-space: nowrap;
  }

  /* Product side */
  .card--product {
    display: flex; flex-direction: column; align-items: center; justify-content: center;
    text-align: center;
  }
  .product-tagline {
    margin-top: 26px; font-size: 17px; font-weight: 500;
    letter-spacing: 0.08em; color: var(--ink-soft);
  }
  .product-rule {
    width: 60px; height: 2px; background: var(--accent); margin: 22px auto 0;
  }
  .product-web {
    margin-top: 18px; font-size: 15px; letter-spacing: 0.06em; color: var(--accent);
  }

  /* Contact side */
  .card--contact .brand {
    position: absolute; left: 48px; top: 50%; transform: translateY(-50%);
  }
  .card--contact .brand-name { font-size: 24px; }
  .divider {
    position: absolute; left: 340px; top: 90px;
    width: 2px; height: 220px; background: var(--accent);
  }
  .contact {
    position: absolute; left: 370px; top: 96px; right: 16px;
    white-space: nowrap;
  }
  .contact-name {
    font-size: 26px; font-weight: 500; color: var(--accent);
    text-transform: uppercase; letter-spacing: 0.03em; line-height: 1;
  }
  .contact-title {
    font-size: 15px; font-weight: 500; letter-spacing: 0.06em;
    margin-top: 8px; color: var(--ink-soft);
  }
  .contact-address {
    font-size: 14px; letter-spacing: 0.04em; line-height: 1.5;
    margin-top: 16px; color: var(--ink-soft); font-style: normal;
  }
  .contact-list { list-style: none; margin-top: 12px; }
  .contact-list li {
    display: flex; align-items: center; gap: 10px;
    font-size: 14px; letter-spacing: 0.03em; line-height: 1.75;
    color: var(--ink-soft);
  }
  .contact-list svg {
    width: 13px; height: 13px; flex: none;
    fill: none; stroke: var(--accent); stroke-width: 1.6;
  }
</style>
</head>
<body>
<main class="canvas">
  <section class="card card--product" aria-label="Product side">
    <div class="brand">
      <span class="brand-mark"></span>
      <span class="brand-name">Glimworld</span>
    </div>
    <p class="product-tagline">Culturally Immersive Language Learning Games</p>
    <div class="product-rule"></div>
    <p class="product-web">www.glimworld-play.com</p>
  </section>

  <section class="card card--contact" aria-label="Contact side">
    <div class="brand">
      <span class="brand-mark"></span>
      <span class="brand-name">Brightloom<br>Language</span>
    </div>
    <div class="divider"></div>
    <div class="contact">
      <h1 class="contact-name">Perry Dunmore</h1>
      <p class="contact-title">Founder &amp; CEO</p>
      <address class="contact-address">48 Harrow Field Road<br>Millbrook Falls, TX 75090</address>
      <ul class="contact-list">
        <li>
          <svg viewBox="0 0 16 16" aria-hidden="true"><path d="M4 1.5l2.5 3-1.5 1.8c.8 1.8 2.4 3.4 4.2 4.2L11 9l3 2.5-1.5 2.5C7 14 2 9 2 3.5z"/></svg>
          (555)-014-2286
        </li>
        <li>
          <svg viewBox="0 0 16 16" aria-hidden="true"><rect x="1.5" y="3.5" width="13" height="9" rx="1"/><path d="M1.5 4l6.5 5 6.5-5"/></svg>
          pdunmore@quillpost-mail.net
        </li>
        <li>
          <svg viewBox="0 0 16 16" aria-hidden="true"><circle cx="8" cy="8" r="6.5"/><ellipse cx="8" cy="8" rx="3" ry="6.5"/><path d="M1.5 8h13"/></svg>
          www.glimworld-play.com
        </li>
      </ul>
    </div>
  </section>
</main>
</body>
</html>
```